Professional Single Page Website Design for Tollbrook Advisory

Tollbrook Advisory is a new business consultancy specializing in providing expert services to small businesses, primarily in the brick-and-mortar retail and food service sectors. We offer a range of services including franchise development and launch, due diligence, and construction management.

Currently, we have a basic website set up at www.tollbrookadvisory.example, but we need a professional touch to enhance its design and functionality.

Project Requirements:
- Single Page Design: For now, we need a single page design that effectively showcases who we are, our services, and contact information.
- Future Expansion: The design should be flexible and scalable for future expansion to include additional pages like specific service offerings, about us, and a dedicated contact page.
- Design Aesthetic: We are looking for a modern yet professional design that aligns with our brand identity.
- Logo: We have a logo that we like, which was also sourced from Pixel Bazaar. The logo files are attached to this project brief.

Key Sections to Include:
- Hero Section: An engaging introduction to Tollbrook Advisory with a strong visual impact.
- About Us: A brief overview of who we are and our mission.
- Team: Section for the profiles of the two principals.
- Services: A clear and concise presentation of our services, including franchise development, due diligence, and construction management.
- Contact Information: Easy-to-find contact details, including a form for inquiries.
- Call to Action: Encouraging visitors to get in touch with us for consultations or further information.

Design Considerations:
- Ensure the design is responsive and mobile-friendly.
- Include high-quality images and icons that complement our services and industry.
- We do not need development services, this is only a design project.

```html
<!DOCTYPE html>
<html lang="en">
<head>
<meta charset="utf-8">
<title>Tollbrook Advisory</title>
<link href="https://fonts.googleapis.com/css2?family=Poppins:wght@400;500;600;700&display=swap" rel="stylesheet">
<style>
:root{
  --green:#94c9b1;
  --green-soft:#e6f3ed;
  --navy:#1f2a33;
  --ink:#222a30;
  --text:#333b40;
  --white:#ffffff;
  --sky-a:#3f74bd;
  --sky-b:#6f9fd6;
  --photo-slate:#55636f;
}
*{margin:0;padding:0;box-sizing:border-box}
html,body{width:1200px;height:3225px;overflow:hidden}
body{position:relative;font-family:'Poppins',sans-serif;color:var(--text);background:var(--white)}
.abs{position:absolute}

/* header */
.site-header{position:absolute;left:0;top:0;width:1200px;height:103px;background:var(--white)}
.brand{position:absolute;left:112px;top:30px;display:flex;align-items:center;gap:12px}
.brand-dot{width:40px;height:40px;border-radius:50%;background:var(--green)}
.brand-name{font-weight:600;font-size:22px;color:var(--ink)}
.main-nav{position:absolute;right:110px;top:40px;display:flex;gap:26px;font-size:16px;font-weight:500;color:var(--ink)}

/* hero */
.hero-photo{position:absolute;left:0;top:103px;width:1200px;height:600px;
  background:linear-gradient(100deg,var(--sky-a) 0%,var(--sky-b) 45%,#c9d6e3 62%,#eef1f4 80%,#b9c2cc 100%)}
.hero-cut{position:absolute;left:0;top:640px}
.hero-copy{position:absolute;left:109px;top:218px;width:440px;color:var(--white)}
.hero-welcome{font-size:32px;font-weight:400;line-height:1.2}
.hero-title{font-size:48px;font-weight:700;color:var(--green);margin-top:8px;line-height:1.2}
.hero-text{font-size:15.5px;font-weight:500;line-height:26px;margin-top:30px;text-align:justify}

/* section titles */
.section-title{position:absolute;left:0;width:1200px;text-align:center;font-size:42px;font-weight:600;color:var(--green)}
.section-intro{position:absolute;left:0;width:1200px;text-align:center;font-size:16px;line-height:29px;color:var(--ink)}

/* services */
.service-card{position:absolute;top:1020px;width:299px;height:220px;background:var(--navy);border-radius:18px;text-align:center;color:var(--white)}
.service-icon{position:absolute;left:92px;top:-62px;width:115px;height:115px;border-radius:50%;background:var(--green);border:5px solid var(--green-soft);display:flex;align-items:center;justify-content:center}
.service-name{position:absolute;left:0;top:80px;width:100%;font-size:17.5px;font-weight:600;color:var(--green);line-height:25px}
.service-desc{position:absolute;left:10px;top:144px;width:279px;font-size:13px;line-height:20px}
.btn-dark{position:absolute;width:150px;height:43px;background:var(--navy);color:var(--white);font-size:16px;display:flex;align-items:center;justify-content:center;border-radius:3px;box-shadow:0 3px 6px rgba(0,0,0,.25)}

/* about */
.about-band{position:absolute;left:0;top:1415px;width:1200px;height:589px;background:linear-gradient(110deg,#eef2f2 0%,#f6f9f9 40%,#eef6f3 100%)}
.divider-line{position:absolute;left:599px;top:1388px;width:2px;height:96px;background:var(--ink)}
.about-text{position:absolute;left:160px;top:1566px;width:880px;text-align:center;font-size:16px;line-height:28.2px;color:var(--ink)}
.pillar{position:absolute;top:1839px;width:468px;padding-left:30px;border-left:7px solid var(--ink)}
.pillar h3{font-size:24px;font-weight:600;color:var(--green);line-height:1;margin-top:-2px}
.pillar p{font-size:16px;line-height:23px;color:var(--ink);margin-top:8px;text-align:justify}

/* team */
.team-photo{position:absolute;top:2174px;width:451px;height:312px;border-radius:38px;background:linear-gradient(180deg,#5a6975,#4d5a66)}
.team-plate{position:absolute;top:2431px;width:320px;height:106px;background:var(--white);text-align:center;box-shadow:0 4px 10px rgba(0,0,0,.12)}
.team-name{font-size:27px;font-weight:600;color:var(--ink);margin-top:12px}
.team-role{font-size:27px;font-weight:400;color:var(--ink);margin-top:2px}

/* footer */
.footer-shape{position:absolute;left:0;top:2626px}
.footer-heading{position:absolute;top:2768px;font-size:24px;font-weight:600;color:var(--white)}
.quick-links{position:absolute;left:111px;top:2812px;list-style:none;color:var(--white);font-size:17.5px}
.quick-links li{height:39.3px}
.social{position:absolute;left:113px;top:3016px;display:flex;gap:6px}
.social span{width:21px;height:21px;border-radius:50%;border:1.5px solid var(--white)}
.v-dash{position:absolute;top:2816px;height:272px;border-left:1.5px dashed #8a959c}
.h-dash{position:absolute;left:354px;width:286px;border-top:1.5px dashed #8a959c}
.contact-icon{position:absolute;left:353px;width:48px;height:48px;border-radius:50%;border:1.5px solid #8a959c;display:flex;align-items:center;justify-content:center}
.contact-block{position:absolute;left:415px;color:var(--white);font-size:15px;line-height:20px}
.contact-block .label{margin-bottom:10px}
.field{position:absolute;left:757px;width:331px;height:43px;background:var(--white);border-radius:2px;padding-left:19px;display:flex;align-items:center;font-size:15px;color:#444}
.submit{position:absolute;left:757px;top:3028px;width:331px;height:43px;background:var(--green);border-radius:2px;display:flex;align-items:center;justify-content:center;font-size:15px;font-weight:500;color:var(--ink)}
.copyright{position:absolute;left:0;top:3159px;width:1200px;height:50px;background:var(--green);text-align:center;line-height:50px;font-size:17.5px;color:var(--ink)}
.footer-base{position:absolute;left:0;top:3209px;width:1200px;height:16px;background:var(--navy)}
</style>
</head>
<body>

<header class="site-header">
  <div class="brand"><span class="brand-dot"></span><span class="brand-name">Tollbrook Advisory</span></div>
  <nav class="main-nav"><span>Home</span><span>About</span><span>Services</span><span>Team</span><span>Contact Us</span></nav>
</header>

<section>
  <div class="hero-photo" role="img" aria-label="Photo of a modern white apartment building with glass balconies against a blue sky"></div>
  <svg class="hero-cut" width="1200" height="90" viewBox="0 0 1200 90">
    <polygon points="0,58 1200,11 1200,90 0,90" fill="#ffffff"/>
    <polygon points="112,56 1200,9 1200,30 112,78" fill="#94c9b1"/>
  </svg>
  <div class="hero-copy">
    <div class="hero-welcome">Welcome To</div>
    <h1 class="hero-title">Tollbrook Advisory</h1>
    <p class="hero-text">Your trusted partner in navigating the complexities of the real estate and small business markets. Founded by industry veterans Rafael Ostrander</p>
  </div>
</section>

<section>
  <h2 class="section-title" style="top:790px">Our Services</h2>
  <p class="section-intro" style="top:866px">Sed ut perspiciatis unde omnis iste natus error sit voluptatem accusantium<br>doloremque laudantium, totam rem aperiam, eaque ipsa quae ab illo inventore veritatis et quasi architecto</p>

  <div class="service-card" style="left:111px">
    <div class="service-icon">
      <svg width="56" height="60" viewBox="0 0 56 60" fill="none" stroke="#1f2a33" stroke-width="2"><rect x="10" y="4" width="36" height="44" rx="2"/><path d="M18 14h20M18 22h20M6 46l10-8 8 6 8-6 8 6 10-8"/></svg>
    </div>
    <div class="service-name">Franchise<br>Development &amp; Launch</div>
    <div class="service-desc">At Tollbrook Advisory, our Franchise Development &amp; Launch service is designed</div>
  </div>

  <div class="service-card" style="left:452px">
    <div class="service-icon">
      <svg width="56" height="56" viewBox="0 0 56 56" fill="none" stroke="#1f2a33" stroke-width="2"><rect x="6" y="6" width="30" height="40" rx="2"/><path d="M12 14h18M12 20h18M12 26h10"/><rect x="24" y="28" width="26" height="20" rx="2"/><path d="M32 28v-4h10v4M24 36h26"/></svg>
    </div>
    <div class="service-name">Due<br>Diligence Services</div>
    <div class="service-desc">Tollbrook offers comprehensive evaluations tailored to your business needs.</div>
  </div>

  <div class="service-card" style="left:792px">
    <div class="service-icon">
      <svg width="56" height="56" viewBox="0 0 56 56" fill="none" stroke="#1f2a33" stroke-width="2"><path d="M4 50h48"/><rect x="8" y="30" width="14" height="20"/><rect x="22" y="12" width="16" height="38"/><rect x="38" y="24" width="12" height="26"/><path d="M12 36h6M12 42h6M27 20h6M27 28h6M27 36h6M42 32h4M42 40h4"/></svg>
    </div>
    <div class="service-name">Building &amp; Construction<br>Management</div>
    <div class="service-desc">Our Building &amp; Construction Management Services oversee every</div>
  </div>

  <div class="btn-dark" style="left:526px;top:1286px">View More</div>
</section>

<section>
  <div class="about-band"></div>
  <div class="divider-line"></div>
  <h2 class="section-title" style="top:1488px">About US</h2>
  <p class="about-text">At Tollbrook Advisory, we are committed to your success. Our approach combines meticulous analysis, strategic insights, and personalized service to help you achieve your business goals. We pride ourselves on our ability to deliver results that exceed expectations, fostering long-term relationships built on trust and excellence.Discover how Tollbrook Advisory can support your business journey. Partner with us and experience the difference our dedication and expertise can make.</p>
  <div class="btn-dark" style="left:525px;top:1732px">Read More</div>
  <div class="pillar" style="left:111px"><h3>Our Mission</h3><p>Sed ut perspiciatis unde omnis iste natus error sit voluptatem accusantium doloremque laudanti</p></div>
  <div class="pillar" style="left:622px"><h3>Our Vision</h3><p>Sed ut perspiciatis unde omnis iste natus error sit voluptatem accusantium doloremque laudanti</p></div>
</section>

<section>
  <h2 class="section-title" style="top:2080px">Our Team</h2>
  <div class="team-photo" style="left:111px" role="img" aria-label="Portrait photo of principal Daniel Orrin"></div>
  <div class="team-plate" style="left:177px"><div class="team-name">Daniel Orrin</div><div class="team-role">Principal</div></div>
  <div class="team-photo" style="left:637px" role="img" aria-label="Portrait photo of principal Rafael Ostrander"></div>
  <div class="team-plate" style="left:703px"><div class="team-name">Rafael Ostrander</div><div class="team-role">Principal</div></div>
</section>

<footer>
  <svg class="footer-shape" width="1200" height="599" viewBox="0 0 1200 599">
    <polygon points="0,67 1200,22 1200,599 0,599" fill="#1f2a33"/>
    <polygon points="0,67 1116,2 1116,22 0,90" fill="#94c9b1"/>
    <polygon points="0,90 1116,22 1200,17 1200,40 0,110" fill="#1f2a33"/>
  </svg>

  <h3 class="footer-heading" style="left:111px">Quick Links</h3>
  <ul class="quick-links"><li>Home</li><li>About Us</li><li>Services</li><li>Team</li><li>Contact Us</li></ul>
  <div class="social" aria-label="Social links"><span></span><span></span><span></span><span></span><span></span></div>
  <div class="v-dash" style="left:295px"></div>

  <h3 class="footer-heading" style="left:354px">Contact Details</h3>
  <div class="contact-icon" style="top:2811px">
    <svg width="18" height="22" viewBox="0 0 18 22"><path d="M9 1a7 7 0 0 0-7 7c0 5 7 13 7 13s7-8 7-13a7 7 0 0 0-7-7z" fill="#94c9b1"/><circle cx="9" cy="8" r="2.5" fill="#1f2a33"/></svg>
  </div>
  <div class="contact-block" style="top:2813px"><div class="label">Address</div>214 Harbor Loop, Suite 5,<br>Lakeview, CA 90000</div>
  <div class="h-dash" style="top:2899px"></div>
  <div class="contact-icon" style="top:2920px">
    <svg width="22" height="16" viewBox="0 0 22 16"><rect width="22" height="16" rx="2" fill="#94c9b1"/><path d="M1 2l10 7 10-7" stroke="#1f2a33" stroke-width="1.6" fill="none"/></svg>
  </div>
  <div class="contact-block" style="top:2920px"><div class="label">Email</div>info@tollbrookadvisory.example</div>
  <div class="h-dash" style="top:2991px"></div>
  <div class="contact-icon" style="top:3012px">
    <svg width="20" height="20" viewBox="0 0 20 20"><path d="M4 1l4 4-2 3c1 3 3 5 6 6l3-2 4 4-3 3C9 19 1 11 1 4z" fill="#94c9b1"/></svg>
  </div>
  <div class="contact-block" style="top:3012px"><div class="label">Phone</div>+1 555 0142 0199</div>
  <div class="v-dash" style="left:697px"></div>

  <h3 class="footer-heading" style="left:757px">Contact Me</h3>
  <div class="field" style="top:2813px">Name:</div>
  <div class="field" style="top:2866px">Company Name:</div>
  <div class="field" style="top:2919px">Email:</div>
  <div class="field" style="top:2971px">Phone Number:</div>
  <div class="submit">Submit Now</div>

  <div class="copyright">Copyrights 2024 Tollbrookadvisory. All Rights Reserved.</div>
  <div class="footer-base"></div>
</footer>

</body>
</html>
```